VELKO Website Redesign in Wix

Task:
Create a new design for all pages of the VELKO technology website in Wix. Specifications are:
Color palette preferences: black, white, gray, purple, blue. See VELKO Ref Doc provided.
Please refer to the VELKO_ref doc for a sample of the desired color palette
Typesetting must be in Montserrat
Brand will be that of a Marketing Technology company
Looking for vibrant, highly engaging images and organized, digestible flow. Open to suggestions
Required format is Wix.
VELKO logo does NOT need to be redesigned. Please use the files provided for the VELKO logo.
Look and feel
Each slider illustrates characteristics of the customer's brand and the style your logo design should communicate.

```html
<!DOCTYPE html>
<html lang="en">
<head>
<meta charset="utf-8">
<title>VELKO – Marketing Technology</title>
<link href="https://fonts.googleapis.com/css2?family=Montserrat:wght@400;500;600;700;800&display=swap" rel="stylesheet">
<style>
:root{
  --purple:#5b0f7c;
  --purple-deep:#3d0a63;
  --navy:#1c2160;
  --navy-band:#1f2a6e;
  --ink:#1d1d1f;
  --grey-bg:#f2f3f5;
  --grey-text:#5c5c66;
  --line:#c9c9cf;
  --footer:#242424;
  --white:#ffffff;
}
*{box-sizing:border-box;margin:0;padding:0}
html,body{width:1200px;height:3715px;overflow:hidden}
body{font-family:'Montserrat',sans-serif;color:var(--ink);position:relative;background:var(--white)}
.abs{position:absolute}
.bar{position:absolute;left:112px;width:94px;height:5px;background:var(--purple)}
.bar.light{background:var(--white)}
.section-title{position:absolute;left:112px;font-weight:700;color:var(--navy);text-transform:uppercase;letter-spacing:.3px}

/* hero */
.hero{position:absolute;left:0;top:0;width:1200px;height:617px;
  background:linear-gradient(100deg,#5a1690 0%,#4a1a8c 45%,#35237e 100%)}
.hero-art{position:absolute;left:560px;top:85px;width:640px;height:532px;
  background:radial-gradient(circle at 60% 45%,rgba(120,110,200,.35),rgba(0,0,0,0) 65%)}
.topbar{position:absolute;left:0;top:0;width:1200px;height:85px;background:rgba(40,20,90,.55)}
.logo{position:absolute;left:112px;top:16px;font-size:50px;font-weight:600;color:var(--white);letter-spacing:12px}
.nav{position:absolute;left:408px;top:35px;display:flex;gap:23px;font-size:14px;font-weight:600;color:var(--white)}
.nav .active{color:#c9c2dc}
.login{position:absolute;left:1025px;top:34px;font-size:14px;color:var(--white);display:flex;align-items:center;gap:6px}
.hero h1{position:absolute;left:112px;top:268px;font-size:42px;font-weight:700;color:var(--white)}
.hero p{position:absolute;left:112px;top:338px;width:440px;font-size:17px;line-height:27px;color:var(--white)}
.dots{position:absolute;left:1102px;top:257px}
.dots span{display:block;width:13px;height:13px;border:2px solid var(--white);border-radius:50%;margin:0 0 14px 60px}
.dots span.on{background:var(--white)}
.dots em{position:absolute;left:0;top:-2px;font-style:normal;font-size:12px;color:var(--white)}

/* strategy */
.strategy{position:absolute;top:617px;left:0;width:1200px;height:471px;background:var(--grey-bg)}
.pillar{position:absolute;width:220px;font-size:16px;font-weight:500;line-height:26px;text-transform:uppercase}
.pillar::before{content:"";position:absolute;left:0;top:-21px;width:52px;height:5px;background:var(--purple)}

/* platform */
.platform{position:absolute;top:1088px;left:0;width:1200px;height:429px;
  background:linear-gradient(90deg,#202a6a 0%,#24307a 60%,#1c2a6a 100%)}
.platform-art{position:absolute;left:560px;top:0;width:640px;height:429px;
  background:radial-gradient(circle at 40% 45%,rgba(110,130,210,.28),rgba(0,0,0,0) 60%)}
.platform p{position:absolute;left:112px;top:203px;width:490px;font-size:15px;line-height:26px;color:var(--white);text-align:justify}

/* partners */
.partner{position:absolute;display:flex;align-items:center;gap:10px;font-size:28px;font-weight:500;color:#555a60}
.partner i{display:block;width:52px;height:52px;border-radius:50%;background:#8b8f94}
.partner.box{background:#5d5d63;color:var(--white);font-size:18px;font-weight:700;padding:0 22px;height:50px}

/* team */
.team{position:absolute;top:2045px;left:0;width:1200px;height:485px;background:var(--grey-bg)}
.team p{position:absolute;left:112px;top:160px;width:450px;font-size:15px;line-height:26px;color:var(--grey-text)}
.member{position:absolute;top:272px;width:300px;height:213px}
.member .hover{position:absolute;inset:0;background:linear-gradient(160deg,rgba(92,20,140,.9),rgba(60,30,120,.9));color:var(--white);text-align:center;padding-top:85px}
.member .hover b{display:block;font-size:16px;font-weight:700}
.member .hover span{display:block;font-size:15px;margin-top:10px}

/* awards */
.awards{position:absolute;top:2530px;left:0;width:1200px;height:377px;
  background:radial-gradient(circle at 62% 45%,#6a2aa8 0%,#5a1690 40%,#4c0c78 100%)}
.stat{position:absolute;top:200px;color:var(--white)}
.stat b{display:block;font-size:34px;font-weight:700}
.stat span{display:block;font-size:21px;line-height:29px;margin-top:18px;text-transform:uppercase}

/* contact */
.field-label{position:absolute;left:110px;font-size:13px;font-weight:500}
.field{position:absolute;left:112px;width:531px;height:41px;border:1px solid var(--line);font-size:13px;color:#777;padding:13px 17px}
.field.msg{height:85px}
.submit{position:absolute;left:424px;top:3452px;width:219px;height:48px;background:linear-gradient(90deg,var(--purple),var(--navy));color:var(--white);font-size:15px;font-weight:700;display:flex;align-items:center;justify-content:center}
.info{position:absolute;left:738px;display:flex;align-items:center;gap:33px;font-size:16px;line-height:28px;color:var(--grey-text)}
.info .ic{width:46px;height:46px;border-radius:50%;background:var(--purple-deep);display:flex;align-items:center;justify-content:center;flex:none}

/* footer */
.footer{position:absolute;top:3570px;left:0;width:1200px;height:145px;background:var(--footer);color:var(--white)}
.copy{position:absolute;left:112px;top:68px;font-size:14px}
.follow{position:absolute;left:0;width:1200px;text-align:center;top:48px;font-size:20px}
.socials{position:absolute;left:0;width:1200px;top:90px;display:flex;justify-content:center;gap:24px;font-size:14px;font-weight:600}
.chat{position:absolute;left:1031px;top:38px;width:58px;height:58px;border-radius:50%;background:var(--white);display:flex;align-items:center;justify-content:center}
.code{position:absolute;left:1133px;top:70px;font-size:11px}
</style>
</head>
<body>

<section class="hero">
  <div class="hero-art" role="img" aria-label="Faint line icons of commerce, travel and security over a hand using a laptop"></div>
  <div class="topbar"></div>
  <div class="logo">VELKO</div>
  <nav class="nav"><span class="active">HOME</span><span>HOW IT WORKS</span><span>VELKO APPLICATIONS</span><span>COMPANY</span><span>CONTACT US</span></nav>
  <div class="login"><svg width="14" height="14" viewBox="0 0 14 14"><circle cx="7" cy="7" r="6.2" fill="none" stroke="#fff" stroke-width="1.4"/><circle cx="7" cy="5.5" r="2.2" fill="#fff"/><path d="M3 11.5a4.5 4 0 0 1 8 0" fill="#fff"/></svg>Log In</div>
  <h1>WELCOME TO VELKO</h1>
  <p>Increase and perfect your connection with consumers using VELKO™'s patented self-service content delivery technology</p>
  <div class="dots"><em>HOME</em><span class="on"></span><span></span><span></span><span></span><span></span><span></span><span></span></div>
</section>

<section class="strategy">
  <div class="bar" style="top:54px"></div>
  <h2 class="section-title" style="top:72px;font-size:32px;line-height:39px">Strategy towards<br>market dominance</h2>
  <div class="pillar" style="left:112px;top:219px">Data &amp; analytics models our value is unlocked</div>
  <div class="pillar" style="left:373px;top:219px">Corporate subscription</div>
  <div class="pillar" style="left:635px;top:219px">Ad tech licensing</div>
  <div class="pillar" style="left:897px;top:219px">Platform integrations</div>
  <div class="pillar" style="left:112px;top:343px">Technology licensing</div>
  <div class="pillar" style="left:373px;top:343px">Advertising campaigns</div>
  <div class="pillar" style="left:635px;top:343px">NFT security</div>
  <div class="pillar" style="left:897px;top:343px">Digital rights management applications</div>
</section>

<section class="platform">
  <div class="platform-art" role="img" aria-label="Network of connected communication icons over a dark blue background"></div>
  <div class="bar light" style="top:75px"></div>
  <h2 class="section-title" style="top:97px;font-size:32px;line-height:39px;color:#fff">Our revolutionary<br>platform</h2>
  <p>Whether you're marketing software, selling a product, or looking to close a deal – find out your target market and quickly modify your campaigns to reach consumers silently and securely. Our platform goes far beyond basic ad optimization to deliver individualized content that immediately increases engagement over any communication medium with embedded tones.</p>
</section>

<section>
  <div class="bar" style="top:1608px"></div>
  <h2 class="section-title" style="top:1627px;font-size:32px;line-height:39px">Our customers<br>&amp; partners</h2>
  <div class="partner" style="left:112px;top:1771px"><i></i>Northvale</div>
  <div class="partner" style="left:362px;top:1780px">Galleria</div>
  <div class="partner box" style="left:590px;top:1775px">BRIGHTGATE LTD</div>
  <div class="partner" style="left:813px;top:1780px;font-size:26px;letter-spacing:2px">MERENO&amp;CASTELL</div>
  <div class="partner" style="left:122px;top:1905px">OSTREL</div>
  <div class="partner" style="left:360px;top:1899px;font-size:17px"><i></i>Advertising agency</div>
  <div class="partner" style="left:595px;top:1905px"><i style="width:30px;height:30px"></i>sonvista</div>
  <div class="partner" style="left:856px;top:1910px">Radio Horizon</div>
</section>

<section class="team">
  <div class="bar" style="top:55px"></div>
  <h2 class="section-title" style="top:80px;font-size:46px;font-weight:800">Our team</h2>
  <p>VELKO™ Technology is a revolutionary platform that uses high frequency tones (known as VELKO packets) imperceptible to the human ear.</p>
  <div class="member" style="left:0;background:#dcdcde" role="img" aria-label="Portrait of a team member in a grey suit"></div>
  <div class="member" style="left:300px;background:#ffffff" role="img" aria-label="Portrait of a team member in a magenta top"></div>
  <div class="member" style="left:600px;background:#7a6a8a" role="img" aria-label="Portrait of Daniel Reeve">
    <div class="hover"><b>DANIEL REEVE</b><span>Chief Information Officer</span></div>
  </div>
  <div class="member" style="left:900px;background:#ffffff" role="img" aria-label="Portrait of a team member holding a tablet"></div>
</section>

<section class="awards">
  <div class="bar light" style="top:67px"></div>
  <h2 class="section-title" style="top:88px;font-size:44px;font-weight:800;color:#fff">Our awards</h2>
  <div class="stat" style="left:112px"><b>102</b><span>Award<br>winnings</span></div>
  <div class="stat" style="left:403px"><b>10K+</b><span>Happy<br>clients</span></div>
  <div class="stat" style="left:677px"><b>40</b><span>Industry<br>media</span></div>
  <div class="stat" style="left:960px"><b>602</b><span>Social<br>campaigns</span></div>
</section>

<section>
  <div class="bar" style="top:2993px"></div>
  <h2 class="section-title" style="top:3017px;font-size:44px;font-weight:800">Get in touch</h2>
  <div class="field-label" style="top:3091px">Enter Your Name*</div>
  <div class="field" style="top:3117px">Name</div>
  <div class="field-label" style="top:3171px">Enter Your Email*</div>
  <div class="field" style="top:3197px">Email</div>
  <div class="field-label" style="top:3251px">Enter Your Subject</div>
  <div class="field" style="top:3277px">Subject</div>
  <div class="field-label" style="top:3331px">Enter Your Message</div>
  <div class="field msg" style="top:3357px">Message</div>
  <div class="submit">SUBMIT</div>

  <div class="info" style="top:3113px"><span class="ic"><svg width="14" height="18" viewBox="0 0 14 18"><path d="M7 1a6 6 0 0 0-6 6c0 4.5 6 10 6 10s6-5.5 6-10a6 6 0 0 0-6-6z" fill="#fff"/><circle cx="7" cy="7" r="2.2" fill="#3d0a63"/></svg></span><span>465, Lrum Ipsum Dolore,<br>United States,</span></div>
  <div class="info" style="top:3187px"><span class="ic"><svg width="14" height="14" viewBox="0 0 14 14"><path d="M3 1l2.5 3-1.5 1.5a8 8 0 0 0 4.5 4.5L10 8.5l3 2.5-1.5 2A10 10 0 0 1 1 2.5z" fill="#fff"/></svg></span><span>1-800-555-0142</span></div>
  <div class="info" style="top:3260px"><span class="ic"><svg width="15" height="11" viewBox="0 0 15 11"><rect width="15" height="11" rx="1" fill="#fff"/><path d="M0 1l7.5 5L15 1" fill="none" stroke="#3d0a63" stroke-width="1.4"/></svg></span><span>info@velkotech.example</span></div>
</section>

<footer class="footer">
  <div class="copy">©2022 VELKO™ &nbsp;| &nbsp;All Rights Reserved</div>
  <div class="follow">Follow Us:</div>
  <div class="socials"><span>Mingle</span><span>Chatter</span><span>Lensly</span><span>Workly</span></div>
  <div class="chat"><svg width="26" height="22" viewBox="0 0 26 22"><path d="M13 2C6.5 2 2 5.8 2 10.5c0 2.5 1.3 4.7 3.4 6.2L4.5 20l4.2-2.1c1.3.4 2.8.6 4.3.6 6.5 0 11-3.8 11-8S19.5 2 13 2z" fill="#3d0a63"/></svg></div>
  <div class="code">C45</div>
</footer>

</body>
</html>
```